Website Quibrel Outdoor

Hi I'm looking for a simple design for a new website. It's outdoor products mainly in category, Boat, Tarpaulin, Fishing, Golf. I have include image and text for 8 products + presentation etc. I want a simple and modern site + fast + Mobile. Wordpress. I'm going to sell through Tradovik so I don't need any WooCommerce but a buy button to Tradovik. I haven set up the Tradovik account yet. My logo i s grey and orange. My goal is to sell in Tradovik US and later EU.

```html
<!DOCTYPE html>
<html lang="en">
<head>
<meta charset="utf-8">
<title>Quibrel Outdoor</title>
<link rel="stylesheet" href="https://fonts.googleapis.com/css2?family=Montserrat:wght@300;400;500;600;700;800&display=swap">
<style>
:root{
  --orange:#f47b20;
  --grey:#6d6e70;
  --grey-dark:#58595b;
  --ink:#2b2b2b;
  --footer:#2f2f30;
  --light:#f2f2f2;
  --white:#ffffff;
}
*{box-sizing:border-box;margin:0;padding:0}
html,body{width:1200px;height:4068px;overflow:hidden}
body{font-family:"Montserrat",sans-serif;color:var(--ink);background:var(--white);position:relative}
.abs{position:absolute}
section,header,footer{position:absolute;left:0;width:1200px;overflow:hidden}

/* header */
.site-header{top:0;height:120px;background:var(--white)}
.brand{position:absolute;display:flex;align-items:center;gap:8px;color:var(--orange);font-weight:700;text-transform:uppercase;letter-spacing:1px}
.brand-dot{width:14px;height:14px;border-radius:50%;background:var(--grey);flex:none}
.header-brand{left:131px;top:44px;font-size:21px}
.follow{left:473px;top:28px;font-size:11px;font-weight:500;display:flex;align-items:center;gap:7px}
.social-dot{width:26px;height:26px;border-radius:50%;background:#1f6fb8}
.social-dot.dark{background:#1a1a2e}
.social-dot.sky{background:#2aa3e0}
.search{left:679px;top:22px;width:205px;height:38px;border:1px solid #9a9a9a;font-size:11px;font-style:italic;color:#777;padding:11px 12px}
.search svg{position:absolute;right:10px;top:12px}
.call{left:904px;top:25px;display:flex;align-items:center;gap:12px}
.call-icon{width:32px;height:32px;border-radius:50%;background:var(--orange);display:flex;align-items:center;justify-content:center}
.call small{display:block;font-size:10px;font-weight:500}
.call strong{font-size:17px;font-weight:500}
.nav{top:84px;left:418px;font-size:14px;font-weight:500}
.nav a{text-decoration:none;color:var(--ink);position:absolute;white-space:nowrap}
.nav a.active{color:var(--orange);font-weight:700;border-bottom:2px solid var(--orange);padding-bottom:3px}

/* hero */
.hero{top:120px;height:556px;background:#5d5a58}
.hero-photo{position:absolute;inset:0;background:
  radial-gradient(ellipse 420px 300px at 960px 300px,rgba(40,32,28,.75),rgba(40,32,28,0) 70%),
  radial-gradient(ellipse 700px 140px at 420px 330px,rgba(214,160,170,.55),rgba(214,160,170,0) 75%),
  linear-gradient(180deg,#8c8f95 0%,#3f5a3c 14%,#2e4a2c 26%,#6f7d7a 38%,#a6a3a8 50%,#c0949a 62%,#8a6a6a 78%,#4a3632 100%)}
.hero-title{left:133px;top:165px;font-size:64px;font-weight:800;color:var(--white);letter-spacing:1px}
.hero-text{left:135px;top:250px;font-size:27px;font-weight:500;color:var(--white);line-height:37px}
.btn{display:inline-block;background:var(--orange);color:var(--white);font-weight:700;text-transform:uppercase;text-align:center;text-decoration:none}
.hero-btn{left:134px;top:347px;width:152px;height:48px;line-height:44px;font-size:15px;border:2px solid var(--white)}
.dots{left:562px;top:512px;display:flex;gap:12px;align-items:center}
.dots span{width:6px;height:6px;border-radius:50%;background:var(--white)}
.dots span.on{width:11px;height:11px;border:2px solid var(--orange);background:transparent}

/* section titles */
.section-title{left:0;width:1200px;text-align:center;font-size:25px;font-weight:700;text-transform:uppercase}
.title-mark{width:16px;height:16px;border-radius:50%;margin:0 auto 12px;background:var(--grey)}
.title-rule{width:38px;height:2px;background:var(--grey);margin:10px auto 0}
.on-dark{color:var(--white)}
.on-dark .title-mark,.on-dark .title-rule{background:var(--white)}

/* categories */
.categories{top:676px;height:860px}
.cat{position:absolute;width:459px;height:324px}
.cat span{position:absolute;left:21px;bottom:18px;color:var(--white);font-size:23px;font-weight:800;text-shadow:0 1px 6px rgba(0,0,0,.35)}
.cat-boat{left:133px;top:146px;background:
  radial-gradient(ellipse 200px 70px at 250px 175px,rgba(255,255,255,.9),rgba(255,255,255,0) 80%),
  linear-gradient(180deg,#2f4f7a 0%,#6f8fb5 22%,#d7dde3 45%,#eceae4 58%,#b0a890 75%,#4b4a36 100%)}
.cat-tarp{left:609px;top:146px;background:
  radial-gradient(ellipse 120px 90px at 400px 130px,rgba(40,90,170,.7),rgba(40,90,170,0) 80%),
  radial-gradient(ellipse 260px 110px at 180px 160px,rgba(235,238,242,.85),rgba(235,238,242,0) 80%),
  linear-gradient(180deg,#6c95c8 0%,#a9c0d9 28%,#cfd6dc 50%,#b9bcc0 72%,#3b3b3d 100%)}
.cat-fish{left:133px;top:489px;background:
  radial-gradient(ellipse 90px 130px at 320px 190px,rgba(214,96,34,.9),rgba(214,96,34,0) 80%),
  linear-gradient(180deg,#54614c 0%,#7b8670 35%,#5d6656 60%,#3a3e35 100%)}
.cat-golf{left:609px;top:489px;background:
  radial-gradient(circle at 175px 185px,#f4f4f0 0,#e6e6e0 20px,rgba(230,230,224,0) 30px),
  linear-gradient(180deg,#9fc0d6 0%,#3d5b2a 18%,#587a2e 40%,#78ab32 65%,#5c8d22 100%)}

/* welcome */
.welcome{top:1536px;height:454px;background:var(--grey);color:var(--white)}
.welcome-kicker{left:131px;top:46px;font-size:19px;font-weight:500}
.welcome-title{left:131px;top:72px;font-size:38px;font-weight:800;text-transform:uppercase}
.welcome-rule{left:131px;top:124px;width:128px;height:2px;background:var(--white)}
.welcome-copy{left:131px;top:158px;width:470px;font-size:16px;font-weight:300;line-height:25.6px}
.welcome-btn{left:133px;top:370px;width:127px;height:41px;line-height:37px;font-size:13px;border:2px solid var(--white)}
.welcome-circle{left:627px;top:54px;width:436px;height:436px;border-radius:50%;background:var(--white)}

/* products */
.products{top:1990px;height:600px}
.product{position:absolute;top:157px;width:223px;height:389px;border:1px solid #cfcfcf;background:var(--white)}
.product-art{position:absolute;left:26px;top:26px;width:170px;height:220px}
.product h3{position:absolute;left:0;width:100%;text-align:center;font-size:15px;font-weight:700;color:var(--grey-dark);line-height:19px}
.buy{position:absolute;left:54px;top:325px;width:127px;height:34px;font-size:10px;display:flex;align-items:center;justify-content:center;gap:7px}
.buy i{width:9px;height:9px;border-radius:50%;background:var(--white);display:block}
.arrow{position:absolute;top:346px}

/* promo */
.promo{top:2590px;height:527px;background:
  linear-gradient(120deg,rgba(255,255,255,0) 40%,rgba(255,255,255,.5) 60%,rgba(255,255,255,0) 80%),
  linear-gradient(180deg,#f7f7f7 0%,#e8e8e8 50%,#f4f4f4 100%)}
.promo-title{left:131px;top:120px;font-size:31px;font-weight:800;color:var(--grey);line-height:40px;text-transform:uppercase}
.promo-copy{left:131px;top:252px;width:500px;font-size:16px;font-weight:400;line-height:25.6px;color:var(--grey-dark)}
.promo-btn{left:134px;top:410px;width:128px;height:38px;line-height:38px;font-size:13px}
.promo-photo{left:700px;top:0;width:380px;height:527px;background:
  radial-gradient(ellipse 120px 50px at 190px 50px,rgba(130,110,80,.9),rgba(130,110,80,0) 80%),
  radial-gradient(ellipse 140px 260px at 190px 300px,rgba(140,125,100,.95),rgba(120,105,85,.6) 60%,rgba(120,105,85,0) 100%)}

/* blog */
.blog{top:3117px;height:600px;background:var(--grey)}
.post{position:absolute;top:163px;width:295px;height:386px;background:var(--white)}
.post-photo{height:174px}
.post h3{position:absolute;left:26px;top:209px;font-size:13px;font-weight:700;color:var(--grey-dark);line-height:16px;text-transform:uppercase}
.post p{position:absolute;left:26px;top:255px;width:240px;font-size:10.5px;line-height:17px;color:#444}
.post .btn{position:absolute;left:34px;top:342px;width:80px;height:25px;line-height:25px;font-size:9px}

/* footer */
.site-footer{top:3717px;height:351px;background:var(--footer);color:var(--white)}
.footer-brand{left:134px;top:130px;font-size:30px;letter-spacing:2px;line-height:34px}
.footer-brand .brand-dot{width:18px;height:18px}
.col-title{font-size:12px;font-weight:700}
.col-list{font-size:11px;line-height:20px;font-weight:400;text-transform:uppercase;list-style:none;margin-top:14px}
.contact-row{display:flex;gap:12px;align-items:flex-start;font-size:11px;line-height:15px;position:absolute}
.c-icon{width:24px;height:24px;border-radius:50%;background:var(--white);flex:none;display:flex;align-items:center;justify-content:center}
.copyright{left:0;width:1200px;top:309px;text-align:center;font-size:10px}
</style>
</head>
<body>

<header class="site-header">
  <div class="brand header-brand"><span class="brand-dot"></span>Quibrel Outdoor</div>
  <div class="abs follow">FOLLOW US <span class="social-dot"></span><span class="social-dot sky"></span><span class="social-dot dark"></span></div>
  <div class="abs search">Search Products
    <svg width="12" height="12" viewBox="0 0 12 12"><circle cx="5" cy="5" r="3.8" fill="none" stroke="#555" stroke-width="1.3"/><line x1="8" y1="8" x2="11" y2="11" stroke="#555" stroke-width="1.3"/></svg>
  </div>
  <div class="abs call">
    <span class="call-icon"><svg width="14" height="14" viewBox="0 0 24 24"><path fill="#fff" d="M6.6 10.8a15 15 0 006.6 6.6l2.2-2.2c.3-.3.7-.4 1-.2 1.1.4 2.3.6 3.6.6.6 0 1 .4 1 1V20c0 .6-.4 1-1 1A17 17 0 013 4c0-.6.4-1 1-1h3.5c.6 0 1 .4 1 1 0 1.3.2 2.5.6 3.6.1.3 0 .7-.2 1z"/></svg></span>
    <div><small>CALL US</small><strong>888.888.8888</strong></div>
  </div>
  <nav class="abs nav">
    <a class="active" style="left:0">HOME</a>
    <a style="left:94px">ABOUT US</a>
    <a style="left:215px">PRODUCTS</a>
    <a style="left:345px">SERVICES</a>
    <a style="left:463px">BLOG</a>
    <a style="left:553px">CONTACT US</a>
  </nav>
</header>

<section class="hero">
  <div class="hero-photo" role="img" aria-label="Hand holding a fishing rod over a calm lake at dusk"></div>
  <h1 class="abs hero-title">FISHING</h1>
  <p class="abs hero-text">Lorem Ipsum is simply dummy<br>text of the printing lorem</p>
  <a class="abs btn hero-btn">READ MORE</a>
  <div class="abs dots"><span></span><span></span><span class="on"></span><span></span><span></span></div>
</section>

<section class="categories">
  <h2 class="abs section-title" style="top:46px"><div class="title-mark"></div>Categories<div class="title-rule"></div></h2>
  <div class="cat cat-boat" role="img" aria-label="White motor yacht cruising on the water"><span>BOAT</span></div>
  <div class="cat cat-tarp" role="img" aria-label="Boats covered with tarpaulins in winter storage"><span>TARPAULIN</span></div>
  <div class="cat cat-fish" role="img" aria-label="Angler in an orange jacket by a forest river"><span>FISHING</span></div>
  <div class="cat cat-golf" role="img" aria-label="Golf ball at the edge of the hole on a green"><span>GOLF</span></div>
</section>

<section class="welcome">
  <p class="abs welcome-kicker">WELCOME TO</p>
  <h2 class="abs welcome-title">Quibrel Outdoor</h2>
  <div class="abs welcome-rule"></div>
  <p class="abs welcome-copy">There are many variations of passages of Lorem Ipsum available, but the majority have suffered alteration in some form, by injected humour, or randomised words which don't look even slightly believable. If you are going to use a passage of Lorem Ipsum, you need to be sure there isn't anything embarrassing hidden n the middle of text.</p>
  <a class="abs btn welcome-btn">READ MORE</a>
  <div class="abs welcome-circle"></div>
</section>

<section class="products">
  <h2 class="abs section-title" style="top:41px"><div class="title-mark"></div>Our Products<div class="title-rule"></div></h2>
  <svg class="arrow" style="left:70px" width="12" height="22" viewBox="0 0 12 22"><polyline points="11,1 1,11 11,21" fill="none" stroke="#888" stroke-width="1.5"/></svg>
  <svg class="arrow" style="left:1106px" width="12" height="22" viewBox="0 0 12 22"><polyline points="1,1 11,11 1,21" fill="none" stroke="#888" stroke-width="1.5"/></svg>

  <div class="product" style="left:131px">
    <div class="product-art" role="img" aria-label="Sunglasses on a lanyard clip" style="background:radial-gradient(ellipse 55px 90px at 85px 120px,#d8d6e4,#eceaf2 55%,rgba(255,255,255,0) 100%)"></div>
    <h3 style="top:294px">GLASSES</h3>
    <a class="btn buy"><i></i>BUY TRADOVIK</a>
  </div>
  <div class="product" style="left:368px">
    <div class="product-art" role="img" aria-label="Clear water bag used as tarpaulin weight" style="background:radial-gradient(ellipse 75px 80px at 85px 110px,#cfcfcb,#e6e6e3 55%,rgba(255,255,255,0) 100%)"></div>
    <h3 style="top:272px">TRAPAULIN<br>WEIGHT BAG</h3>
    <a class="btn buy"><i></i>BUY TRADOVIK</a>
  </div>
  <div class="product" style="left:606px">
    <div class="product-art" role="img" aria-label="Grey microfibre towel with a clip" style="background:radial-gradient(ellipse 40px 95px at 85px 110px,#8d8e91,#c4c5c7 55%,rgba(255,255,255,0) 100%)"></div>
    <h3 style="top:290px">TOWEL</h3>
    <a class="btn buy"><i></i>BUY TRADOVIK</a>
  </div>
  <div class="product" style="left:845px">
    <div class="product-art" role="img" aria-label="Tan tent with orange guy line tensioners" style="background:radial-gradient(ellipse 70px 55px at 70px 110px,#c9a04a,#e2c88e 55%,rgba(255,255,255,0) 100%)"></div>
    <h3 style="top:290px">TOWEL</h3>
    <a class="btn buy"><i></i>BUY TRADOVIK</a>
  </div>
</section>

<section class="promo">
  <h2 class="abs promo-title">Lorem Ipsum is simply<br>dummy text of the<br>printing</h2>
  <p class="abs promo-copy">It is a long established fact that a reader will be distracted by the readable content of a page when looking at its layout. The point of using Lorem Ipsum is that it has a more-or-less normal distribution of letters, as opposed to using 'Content here, content here', making it look like readable</p>
  <a class="abs btn promo-btn">READ MORE</a>
  <div class="abs promo-photo" role="img" aria-label="Angler in a hat and fishing vest holding a rod"></div>
</section>

<section class="blog">
  <h2 class="abs section-title on-dark" style="top:46px"><div class="title-mark"></div>Latest Blog<div class="title-rule"></div></h2>
  <article class="post" style="left:131px">
    <div class="post-photo" role="img" aria-label="Man fishing from a boat deck" style="background:radial-gradient(ellipse 60px 70px at 200px 80px,rgba(30,34,45,.85),rgba(30,34,45,0) 80%),linear-gradient(180deg,#cfd3d8 0%,#9aa0a6 55%,#5b5e63 100%)"></div>
    <h3>Lorem Ipsum is simply<br>dummy text</h3>
    <p>It is a long established fact that a reader will be distracted by the readable content of a page when looking at its layout. The point of using</p>
    <a class="btn">READ MORE</a>
  </article>
  <article class="post" style="left:453px">
    <div class="post-photo" role="img" aria-label="Boat helm with steering wheel and throttle" style="background:radial-gradient(ellipse 90px 70px at 140px 100px,#8a8a8a,rgba(138,138,138,0) 80%),linear-gradient(180deg,#f0f0f0,#bdbdbd 60%,#6e6e6e)"></div>
    <h3>Lorem Ipsum is simply<br>dummy text</h3>
    <p>It is a long established fact that a reader will be distracted by the readable content of a page when looking at its layout. The point of using</p>
    <a class="btn">READ MORE</a>
  </article>
  <article class="post" style="left:774px">
    <div class="post-photo" role="img" aria-label="Close-up of blue and white tarpaulin fabric" style="background:linear-gradient(135deg,#2b58a8 0%,#5b84c8 25%,#d4e0f0 50%,#9db7de 65%,#2c55a0 100%)"></div>
    <h3>Lorem Ipsum is simply<br>dummy text</h3>
    <p>It is a long established fact that a reader will be distracted by the readable content of a page when looking at its layout. The point of using</p>
    <a class="btn">READ MORE</a>
  </article>
</section>

<footer class="site-footer">
  <div class="brand footer-brand"><span class="brand-dot"></span>Quibrel<br>Outdoor</div>

  <div class="abs" style="left:431px;top:59px">
    <p class="col-title">MENU</p>
    <ul class="col-list">
      <li>Home</li><li>About us</li><li>Products</li><li>Services</li><li>Blog</li><li>Contact us</li>
    </ul>
  </div>

  <p class="abs col-title" style="left:644px;top:59px">CONTACT US</p>
  <div class="contact-row" style="left:644px;top:96px"><span class="c-icon"><svg width="10" height="12" viewBox="0 0 10 12"><path d="M5 0a4 4 0 014 4c0 3-4 8-4 8S1 7 1 4a4 4 0 014-4z" fill="#2f2f30"/><circle cx="5" cy="4" r="1.4" fill="#fff"/></svg></span><span>2150 Larkmoor Lane<br>Fenwick, CA 90412</span></div>
  <div class="contact-row" style="left:644px;top:147px"><span class="c-icon"><svg width="11" height="11" viewBox="0 0 24 24"><path fill="#2f2f30" d="M6.6 10.8a15 15 0 006.6 6.6l2.2-2.2c.3-.3.7-.4 1-.2 1.1.4 2.3.6 3.6.6.6 0 1 .4 1 1V20c0 .6-.4 1-1 1A17 17 0 013 4c0-.6.4-1 1-1h3.5c.6 0 1 .4 1 1 0 1.3.2 2.5.6 3.6.1.3 0 .7-.2 1z"/></svg></span><span>Call Us<br>888.888.8888</span></div>
  <div class="contact-row" style="left:644px;top:198px"><span class="c-icon"><svg width="12" height="9" viewBox="0 0 12 9"><rect x="0.5" y="0.5" width="11" height="8" fill="#2f2f30"/><polyline points="1,1 6,5 11,1" fill="none" stroke="#fff" stroke-width="1"/></svg></span><span>E mail Us<br>info@QuibrelOutdoor.com</span></div>

  <p class="abs col-title" style="left:963px;top:59px">FOLLOW US</p>
  <div class="contact-row" style="left:963px;top:96px"><span class="c-icon"></span><span>Like us on<br>FRIENDNET</span></div>
  <div class="contact-row" style="left:963px;top:147px"><span class="c-icon"></span><span>Follow us on<br>CHIRPLY</span></div>
  <div class="contact-row" style="left:963px;top:198px"><span class="c-icon"></span><span>Follow us on<br>WORKWEB</span></div>

  <p class="abs copyright">Copyright © 2021 All Rights Reserved</p>
</footer>

</body>
</html>
```